New Business Card for our Indoor Golf Training Facility

We are looking for designs for a new business card for our indoor golf training facility. Attached is our logo, our logo with our slogan, and here is our elevator pitch (What makes us different from the others) not sure if all the info will fit on one card, maybe you can condense the elevator pitch? here is the info

Elevator Pitch
We work with serious golfers and those that want to be serious golfers…
to make you better, faster, at all phases of the game…
We use the same state-of-the-art technology as professional golfers…
which produces data sets that shows your improvement in real time.
Our facility is available 24/7 to our members, which allows you to improve on your time.

our website: www.birchpinlinks.com

Target Market(s)

Golfers

Font styles to use
Serif
Sans Serif

Colors
ec1f27
f59195
fbd4d5
919191
d3d3d3
1b1b1b

Requirements
Must have
• our logo or our logo with the slogan, elevator pitch (can be condensed or shortened)

```html
<!DOCTYPE html>
<html lang="en">
<head>
<meta charset="utf-8">
<title>Birch Pin Links — Business Card</title>
<link rel="stylesheet" href="https://fonts.googleapis.com/css2?family=Oswald:wght@500&family=Roboto:wght@400;500&family=Work+Sans:wght@400;500&display=swap">
<style>
  :root {
    --red: #ec1f27;
    --pink: #f59195;
    --blush: #fbd4d5;
    --grey: #919191;
    --light-grey: #d3d3d3;
    --card: #1b1b1b;
    --backdrop: #2b2b2b;
    --white: #ffffff;
  }
  * { margin: 0; padding: 0; box-sizing: border-box; }
  html, body {
    width: 1200px; height: 900px; overflow: hidden;
    background: var(--backdrop);
  }
  .sheet {
    width: 1200px; height: 900px;
    display: flex; flex-direction: column; align-items: center; justify-content: center;
    gap: 44px;
  }
  .card {
    width: 700px; height: 400px;
    background: linear-gradient(160deg, #222 0%, var(--card) 55%, #151515 100%);
    box-shadow: 0 14px 30px rgba(0,0,0,.45);
    position: relative;
    color: var(--white);
  }

  /* Pitch side */
  .card--pitch {
    display: flex; flex-direction: column; align-items: center;
    padding-top: 66px;
    font-family: "Roboto", sans-serif;
  }
  .brand__name {
    font-family: "Roboto", sans-serif; font-weight: 500;
    font-size: 38px; color: var(--light-grey); letter-spacing: .5px;
    line-height: 1.1;
  }
  .brand__slogan {
    font-size: 14px; color: var(--red); letter-spacing: .6px;
    margin-top: 8px;
  }
  .pitch { margin-top: 26px; text-align: center; }
  .pitch__title {
    font-size: 16px; color: var(--red); margin-bottom: 6px; font-weight: 500;
  }
  .pitch__line { font-size: 13.5px; line-height: 1.5; color: var(--white); }

  /* Contact side */
  .card--contact { font-family: "Work Sans", sans-serif; }
  .identity {
    position: absolute; right: 340px; top: 148px; text-align: right;
    white-space: nowrap;
  }
  .identity__name {
    font-family: "Oswald", sans-serif; font-weight: 500;
    font-size: 40px; color: var(--red); letter-spacing: 1px; line-height: 1.05;
  }
  .identity__role { font-size: 18px; color: var(--white); margin-top: 2px; }
  .divider {
    position: absolute; left: 382px; top: 152px;
    width: 2px; height: 68px; background: var(--white);
  }
  .contacts {
    position: absolute; left: 410px; top: 148px;
    list-style: none; font-size: 18px; line-height: 1.45;
    white-space: nowrap;
  }
  .contacts li { display: flex; align-items: center; gap: 10px; }
  .contacts svg { width: 13px; height: 13px; flex: none; }
  .contacts .accent { color: var(--red); }
  .address {
    position: absolute; left: 0; right: 0; bottom: 54px;
    text-align: center; font-size: 18px; letter-spacing: .6px;
  }
</style>
</head>
<body>
<main class="sheet">

  <section class="card card--pitch">
    <p class="brand__name">Birch Pin Links</p>
    <p class="brand__slogan">Par Is Good. Under Is Better. Be Better.</p>
    <div class="pitch">
      <h2 class="pitch__title">Elevator Pitch</h2>
      <p class="pitch__line">We work with serious golfers and those that want to be serious golfers…</p>
      <p class="pitch__line">to make you better, faster, at all phases of the game…</p>
      <p class="pitch__line">We use the same state-of-the-art technology as professional golfers…</p>
      <p class="pitch__line">which produces data sets that shows your improvement in real time.</p>
      <p class="pitch__line">Our facility is available 24/7 to our members, which allows you to improve on your time.</p>
    </div>
  </section>

  <section class="card card--contact">
    <div class="identity">
      <h1 class="identity__name">DANIEL BROOKS</h1>
      <p class="identity__role">Director</p>
    </div>
    <span class="divider"></span>
    <ul class="contacts">
      <li>
        <svg viewBox="0 0 24 24" aria-hidden="true"><path fill="#ec1f27" d="M6.6 10.8a15 15 0 0 0 6.6 6.6l2.2-2.2c.3-.3.7-.4 1-.2 1.1.4 2.3.6 3.6.6.6 0 1 .4 1 1V20c0 .6-.4 1-1 1A17 17 0 0 1 3 4c0-.6.4-1 1-1h3.5c.6 0 1 .4 1 1 0 1.3.2 2.5.6 3.6.1.3 0 .7-.2 1z"/></svg>
        555-014-2290
      </li>
      <li>
        <svg viewBox="0 0 24 24" aria-hidden="true"><rect x="2.5" y="5" width="19" height="14" rx="1.5" fill="none" stroke="#ec1f27" stroke-width="2"/><path d="M3 6l9 7 9-7" fill="none" stroke="#ec1f27" stroke-width="2"/></svg>
        info@birchpinlinks.com
      </li>
      <li>
        <svg viewBox="0 0 24 24" aria-hidden="true"><circle cx="12" cy="12" r="9.5" fill="none" stroke="#ec1f27" stroke-width="2"/><path d="M2.5 12h19M12 2.5c3 3 3 16 0 19M12 2.5c-3 3-3 16 0 19" fill="none" stroke="#ec1f27" stroke-width="1.6"/></svg>
        <span>www.<span class="accent">birchpinlinks</span>.com</span>
      </li>
    </ul>
    <p class="address">1480 W. Alder Rd. Unit B4 Maple Grove, OH 45000</p>
  </section>

</main>
</body>
</html>
```